KRL Stationery Design Project

Dear Designers,
We need a new stationery design for company to match our new logo.
Designers should provide a design for the following:
1. Business Card: 3.5x2 Inches.
2. Letterhead: A4 size.
3. Envelops: 25x35.5 Cm.
You can keep the Arabic name at the bottom of the logo Or you can use the separate attached Arabic Name.
Please refer to the attached logo guide for design information.
Sample Business Card information:
Name: Tarek Sowan
Position: Operation Manager
Tel: +966 920007164 Ex. 500
Fax: +966 (3)8842617
Mob: +966 (5)00263817
email: tarek@krl-example.com.sa
URL: www.krl-example.com.sa
Address:
Nakheel Heights, Suite 718
Zayed bin Omar Str.
Khobar, 31847
Saudi Arabia
Updates
Dear All,
Please note, we had uploaded our logo along with Arabic writing in Adobe illustrator format (.ai).
Regards,
Karim
Dear All,
A sample data for the business card had been added as per your request.
Regards,
Karim

```html
<!DOCTYPE html>
<html lang="en">
<head>
<meta charset="utf-8">
<title>KRL Business Card</title>
<link href="https://fonts.googleapis.com/css2?family=Source+Sans+3:wght@400;700&display=swap" rel="stylesheet">
<style>
  :root {
    --backdrop: #1e1e1e;
    --card: #ffffff;
    --navy: #0f2f55;
    --grey-band: #a9a9a9;
    --ink: #333333;
  }
  * { margin: 0; padding: 0; box-sizing: border-box; }
  html, body { width: 960px; height: 1200px; overflow: hidden; }
  body {
    background: var(--backdrop);
    font-family: "Source Sans 3", Arial, sans-serif;
    position: relative;
  }
  .card {
    position: absolute;
    left: 57px;
    width: 840px;
    height: 478px;
    background: var(--card);
    border-radius: 32px;
    overflow: hidden;
  }
  .card--front { top: 80px; }
  .card--back { top: 625px; }

  .brand {
    position: absolute;
    display: flex;
    align-items: center;
    gap: 18px;
    color: var(--navy);
    font-weight: 700;
    line-height: 1;
  }
  .brand__mark {
    width: 34px; height: 34px;
    background: var(--navy);
  }
  .brand__name { font-size: 120px; letter-spacing: 4px; }
  .card--front .brand { left: 80px; top: 110px; }
  .card--back .brand { left: 50%; top: 175px; transform: translateX(-50%); }

  .contact {
    position: absolute;
    left: 559px;
    top: 110px;
    color: var(--ink);
    font-size: 21px;
    line-height: 29px;
  }
  .contact__name { color: var(--navy); font-size: 28px; line-height: 34px; }
  .contact__role { color: var(--navy); font-size: 21px; margin-bottom: 12px; }
  .contact__line b { font-style: italic; font-weight: 700; }
  .contact__phones { margin-bottom: 6px; }
  .contact__phones div { margin-bottom: 6px; }
  .contact__address { line-height: 29px; }

  .bands { position: absolute; left: 0; top: 0; }
  .band-text {
    position: absolute;
    font-size: 27px;
    line-height: 1;
  }
  .band-text--email { left: 30px; top: 363px; color: #ffffff; }
  .band-text--web { left: 501px; top: 392px; color: var(--navy); }
</style>
</head>
<body>
  <section class="card card--front">
    <svg class="bands" width="840" height="478" viewBox="0 0 840 478" aria-hidden="true">
      <polygon points="440,378 840,378 840,434 388,434" fill="var(--grey-band)"/>
      <polygon points="0,348 491,348 440,404 0,404" fill="var(--navy)"/>
    </svg>
    <div class="brand">
      <span class="brand__name">KRL</span>
      <span class="brand__mark"></span>
    </div>
    <div class="contact">
      <div class="contact__name">Your Name</div>
      <div class="contact__role">Designation</div>
      <div class="contact__phones">
        <div class="contact__line"><b>t</b> : 123-123-1234</div>
        <div class="contact__line"><b>f</b> : 123-123-1234</div>
      </div>
      <div class="contact__address">
        1234, Suite# 123<br>Street Name<br>Country Code
      </div>
    </div>
    <div class="band-text band-text--email">info@krl-example.com.sa</div>
    <div class="band-text band-text--web">www.krl-example.com.sa</div>
  </section>

  <section class="card card--back">
    <div class="brand">
      <span class="brand__name">KRL</span>
      <span class="brand__mark"></span>
    </div>
  </section>
</body>
</html>
```